Business Card Design for Training Business

Clear Path Coaching is a new business that delivers training and other services with a focus on topics related to mental health and wellbeing, for example, Wellmind Response Course, Resilience etc. We have a strong focus on evidence-based psychology and neuroscience. I have a logo which I will upload with the brief, so please consider colours that work well with the logo.
Target Market(s)
Adults, workplaces (particularly government and not-for-profits)
Industry/Entity Type
Business
Contact Information for Business Card
Head Strong TrainingSamantha SellwoodDirector0438 770 bec@clearpathcoaching.example.au.auwww.headstrongtraining.com.au

```html
<!DOCTYPE html>
<html lang="en">
<head>
<meta charset="utf-8">
<title>Clear Path Coaching – Business Card</title>
<link rel="stylesheet" href="https://fonts.googleapis.com/css2?family=Raleway:wght@200&family=Open+Sans:wght@400;600&family=Encode+Sans+Condensed:wght@400&display=swap">
<style>
  :root {
    --teal: #1fbcc0;
    --teal-soft: #bfe6e6;
    --paper: #ffffff;
    --ink: #111111;
    --trim: #e0474c;
  }
  html, body {
    margin: 0;
    padding: 0;
    width: 1200px;
    height: 740px;
    overflow: hidden;
    background: var(--paper);
  }
  .canvas {
    position: relative;
    width: 1200px;
    height: 740px;
    background: var(--paper);
  }
  .card {
    position: absolute;
    left: 19px;
    top: 20px;
    width: 1164px;
    height: 702px;
    background: linear-gradient(to bottom,
      var(--teal) 0px, var(--teal) 55px,
      var(--paper) 55px, var(--paper) 258px,
      var(--teal-soft) 400px,
      var(--teal) 585px, var(--teal) 100%);
  }
  .trim-line {
    position: absolute;
    left: 44px;
    top: 44px;
    width: 1112px;
    height: 650px;
    border: 1px solid var(--trim);
    box-sizing: border-box;
  }
  .brand-mark {
    position: absolute;
    left: 97px;
    top: 127px;
    width: 216px;
    height: 216px;
    border-radius: 50%;
    background: var(--teal);
  }
  .brand-name {
    position: absolute;
    left: 338px;
    top: 168px;
    margin: 0;
    font-family: "Raleway", sans-serif;
    font-weight: 200;
    color: var(--ink);
    line-height: 1;
  }
  .brand-name .primary {
    display: block;
    font-size: 66px;
    letter-spacing: 4px;
  }
  .brand-name .secondary {
    display: block;
    margin-top: 18px;
    font-size: 26px;
    letter-spacing: 21px;
  }
  .person {
    position: absolute;
    right: 105px;
    top: 352px;
    text-align: right;
    font-family: "Open Sans", sans-serif;
    color: var(--ink);
  }
  .person-name {
    margin: 0;
    font-size: 29px;
    font-weight: 400;
    letter-spacing: 3px;
    line-height: 1.1;
  }
  .person-role {
    margin: 0;
    font-size: 19px;
    font-weight: 600;
    letter-spacing: 3px;
    line-height: 1.3;
  }
  .contact-list {
    position: absolute;
    right: 105px;
    top: 446px;
    margin: 0;
    padding: 0;
    list-style: none;
    font-family: "Encode Sans Condensed", sans-serif;
    color: var(--ink);
  }
  .contact-item {
    display: flex;
    justify-content: flex-end;
    align-items: center;
    height: 50px;
    font-size: 28px;
  }
  .contact-item.web { font-size: 22px; }
  .contact-item .icon {
    width: 34px;
    height: 34px;
    margin-left: 20px;
    flex: none;
  }
</style>
</head>
<body>
<main class="canvas">
  <section class="card">
  </section>
  <div class="trim-line"></div>

  <div class="brand-mark" aria-hidden="true"></div>
  <h1 class="brand-name">
    <span class="primary">CLEAR PATH</span>
    <span class="secondary">COACHING</span>
  </h1>

  <div class="person">
    <p class="person-name">REBECCA TANFIELD</p>
    <p class="person-role">Director</p>
  </div>

  <ul class="contact-list">
    <li class="contact-item phone">
      <span>+353 1 508 2364</span>
      <svg class="icon" viewBox="0 0 34 34" aria-hidden="true">
        <circle cx="17" cy="17" r="17" fill="#111"/>
        <path d="M11 9.5c1-.8 2.2-.7 2.8.3l1.6 2.6c.5.9.2 1.8-.6 2.4l-1 .7c.8 2 2.6 3.9 4.6 4.8l.8-1c.6-.8 1.6-1 2.4-.5l2.6 1.6c1 .6 1.1 1.8.3 2.8-1.6 2-4 2.6-6.8.9-3.2-1.9-5.8-4.6-7.5-7.8-1.4-2.6-.9-5 .8-6.8z" fill="#fff"/>
      </svg>
    </li>
    <li class="contact-item web">
      <span>www.clearpathcoaching.example.au</span>
      <svg class="icon" viewBox="0 0 34 34" aria-hidden="true">
        <circle cx="17" cy="17" r="17" fill="#111"/>
        <g fill="none" stroke="#fff" stroke-width="1.6">
          <circle cx="17" cy="17" r="9"/>
          <ellipse cx="17" cy="17" rx="4" ry="9"/>
          <line x1="8" y1="17" x2="26" y2="17"/>
          <line x1="9.5" y1="12.5" x2="24.5" y2="12.5"/>
          <line x1="9.5" y1="21.5" x2="24.5" y2="21.5"/>
        </g>
      </svg>
    </li>
    <li class="contact-item email">
      <span>bec@clearpathcoaching.example.au</span>
      <svg class="icon" viewBox="0 0 34 34" aria-hidden="true">
        <circle cx="17" cy="17" r="17" fill="#111"/>
        <g fill="none" stroke="#fff" stroke-width="1.8" stroke-linejoin="round">
          <rect x="8" y="11" width="18" height="12" rx="1"/>
          <polyline points="8,11 17,18 26,11"/>
          <line x1="8" y1="23" x2="14" y2="16.5"/>
          <line x1="26" y1="23" x2="20" y2="16.5"/>
        </g>
      </svg>
    </li>
    <li class="contact-item address">
      <span>24 Harbour Lane, Quay Street, Dublin, D04 K215</span>
      <svg class="icon" viewBox="0 0 34 34" aria-hidden="true">
        <circle cx="17" cy="17" r="17" fill="#111"/>
        <path d="M17 7c-3.9 0-7 3-7 6.9 0 5 7 13.1 7 13.1s7-8.1 7-13.1C24 10 20.9 7 17 7z" fill="#fff"/>
        <circle cx="17" cy="14" r="2.6" fill="#111"/>
      </svg>
    </li>
  </ul>
</main>
</body>
</html>
```